Elegant Business Card with Logo and Picture

Please create a business card that has the Logo colors add Gold and turquoise / use the attached logo - I would like a beautiful Business Card - Please make sure it's printed on both sides / Picture can go on one side Logo other
www.velmoragrove.com
614-372-0583
Lina Suzette Brolin
linasb@quorvamail.com
Life Coach
Thessing Certified Teacher / Life Coach / Interior Designer
Transformational Retreats

Target Market(s)

Women Men General

Industry/Entity Type

Life Coaching

Contact Information for Business Card

www.velmoragrove.com
614-372-0583
Lina Suzette Brolin
Life Coach
Thessing Certified Teacher / Yoga Teacher / Interior Designer

Font styles to use
Serif
Decorative

Colors
33a6d6
e34197
ffc214

Requirements
Must have
• Quality Paper and touch /
Nice to have
• Beautiful Touch and feel
Should not have
• needs to be elegant

```html
<!DOCTYPE html>
<html lang="en">
<head>
<meta charset="utf-8">
<title>Velmora Grove Coaching – Business Card</title>
<link rel="stylesheet" href="https://fonts.googleapis.com/css2?family=Zilla+Slab:ital,wght@0,300;0,400;1,400&family=Great+Vibes&display=swap">
<style>
  :root {
    --backdrop: #2b2d32;
    --peach-deep: #e49a7a;
    --peach-mid: #eeb195;
    --peach-light: #f8d6c5;
    --teal: #3dbdb5;
    --name-coral: #e27c55;
    --ink-grey: #6a6a6a;
    --ink-dark: #3b302b;
    --paper: #ffffff;
    --rule: #ffffff;
  }
  * { box-sizing: border-box; margin: 0; padding: 0; }
  html, body { width: 1200px; height: 900px; overflow: hidden; }
  body {
    background: var(--backdrop);
    font-family: "Zilla Slab", Georgia, serif;
    display: flex;
    flex-direction: column;
    align-items: center;
    justify-content: center;
    gap: 56px;
  }
  .card {
    position: relative;
    width: 660px;
    height: 378px;
    overflow: hidden;
    box-shadow: 0 10px 30px rgba(0,0,0,.45);
  }

  /* Contact side */
  .card--front { background: var(--paper); }
  .front-swoop { position: absolute; inset: 0; width: 100%; height: 100%; }
  .portrait {
    position: absolute;
    left: 90px;
    top: 56px;
    width: 150px;
    height: 150px;
    border-radius: 50%;
    background: radial-gradient(circle at 50% 40%, #e3c39a 0%, #c9a27c 35%, #d8d8d8 70%);
  }
  .details {
    position: absolute;
    left: 264px;
    top: 70px;
    padding-left: 16px;
    border-left: 2px solid var(--teal);
    color: var(--ink-grey);
    font-size: 18px;
    line-height: 1.25;
  }
  .details__headline { display: flex; align-items: baseline; white-space: nowrap; }
  .details__name {
    font-family: "Great Vibes", cursive;
    color: var(--name-coral);
    font-size: 31px;
    line-height: 1;
    font-weight: 400;
  }
  .details__role { color: var(--teal); font-size: 18px; }
  .sep {
    font-family: "Zilla Slab", Georgia, serif;
    font-style: normal;
    color: var(--teal);
    padding: 0 6px;
  }
  .contact { list-style: none; margin-top: 2px; }
  .contact li { display: flex; align-items: center; gap: 8px; }
  .contact svg { width: 15px; height: 15px; flex: none; }

  /* Brand side */
  .card--back {
    background: linear-gradient(160deg, var(--peach-mid) 0%, var(--peach-light) 38%, var(--peach-mid) 60%, var(--peach-deep) 100%);
  }
  .brand {
    position: absolute;
    left: 0; right: 0; top: 118px;
    display: flex;
    flex-direction: column;
    align-items: center;
  }
  .brand__name {
    color: var(--paper);
    font-weight: 400;
    font-size: 34px;
    line-height: 1.1;
    text-align: center;
  }
  .tagline {
    margin-top: 30px;
    padding-bottom: 10px;
    border-bottom: 1px solid var(--rule);
    font-style: italic;
    font-size: 20px;
    color: var(--ink-dark);
    width: 250px;
    text-align: center;
  }
</style>
</head>
<body>

<section class="card card--front" aria-label="Business card, contact side">
  <svg class="front-swoop" viewBox="0 0 660 378" preserveAspectRatio="none" aria-hidden="true">
    <defs>
      <linearGradient id="swoopFill" x1="0" y1="0" x2="1" y2="1">
        <stop offset="0" stop-color="#e49a7a"/>
        <stop offset="0.45" stop-color="#f8d6c5"/>
        <stop offset="1" stop-color="#e9a586"/>
      </linearGradient>
    </defs>
    <path d="M0 0 L40 0 C30 170 150 300 660 312 L660 378 L0 378 Z" fill="url(#swoopFill)"/>
    <path d="M0 0 L22 0 C20 180 170 320 660 340 L660 378 L0 378 Z" fill="#e49a7a" opacity=".55"/>
  </svg>

  <div class="portrait" role="img" aria-label="Portrait photo of Lina Suzette Brolin"></div>

  <div class="details">
    <div class="details__headline">
      <h1 class="details__name">Lina Suzette Brolin</h1>
      <span class="sep">|</span><span class="details__role">Life Coach</span>
    </div>
    <p>Thessing Certified Teacher<span class="sep">|</span>Yoga Teacher</p>
    <p>Interior Designer</p>
    <ul class="contact">
      <li>
        <svg viewBox="0 0 16 16" aria-hidden="true"><circle cx="8" cy="8" r="7" fill="none" stroke="var(--teal)" stroke-width="1.4"/><path d="M5.5 4.5l1.5 1.6-.8 1c.6 1.2 1.4 2 2.6 2.6l1-.8 1.6 1.5-.9 1.1c-2.8-.4-5.2-2.8-5.7-5.7z" fill="var(--teal)"/></svg>
        614-372-0583
      </li>
      <li>
        <svg viewBox="0 0 16 16" aria-hidden="true"><rect x="1.5" y="3.5" width="13" height="9" fill="none" stroke="var(--teal)" stroke-width="1.4"/><path d="M1.5 3.5L8 9l6.5-5.5" fill="none" stroke="var(--teal)" stroke-width="1.4"/></svg>
        linasb@quorvamail.com
      </li>
      <li>
        <svg viewBox="0 0 16 16" aria-hidden="true"><circle cx="8" cy="8" r="6.8" fill="var(--teal)"/><path d="M1.2 8h13.6M8 1.2c-3 3.5-3 10.1 0 13.6M8 1.2c3 3.5 3 10.1 0 13.6" fill="none" stroke="#fff" stroke-width="1"/></svg>
        www.velmoragrove.com
      </li>
    </ul>
  </div>
</section>

<section class="card card--back" aria-label="Business card, brand side">
  <div class="brand">
    <p class="brand__name">Velmora Grove Coaching</p>
    <p class="tagline">Transformational Retreats</p>
  </div>
</section>

</body>
</html>
```